A business card design for a dental office. We have Two doctors working here. We practice general de

I already have a logo designed for the office with the name and a slogan.
Now I need to create design for a business card using the same logo.
Details Needed on the front side of the card are :
Bernard K. Oswin, DDS
Gerald M Fenwick, DDS
418 Birch Lane
Portland, CT 00000
Phone : 555 019 4831
Fax : 555 019 4832
Website : WWW.BrightmoorToothHaven.Com
Office hours by appointment
On the back side of the card need :
Appointment
Date....................Time...................
With....................................
If unable to keep your appointment, please give 24-48 hours notice in order to avoid broken appointment fee.

Industry/Entity Type

Dental Clinic

Contact Information for Business Card

Bernard K. Oswin, DDS
Gerald M Fenwick, DDS
418 Birch Lane
Portland, CT 00000
Phone : 555 019 4831
Fax : 555 019 4832
Appointment

Requirements
Must have
• Keep the Name and slogan on the logo on the front of the card. You can move them around the Logo and Name/Slogan of business (Oswin Family Dentistry/We give you reasons to smile) as you wish to get a feel of the design.
• Bernard K. Oswin, DDS
• Gerald M Fenwick, DDS
• 418 Birch Lane
• Portland, CT 00000
• Phone : 555 019 4831
• Fax : 555 019 4832
• WWW.BrightmoorToothHaven.Com
• Keep these three groups above as they are together now in different areas of the front side.
• On the back side of the card need :
• Appointment
• Date....................Time...................
• With....................................
• If unable to keep your appointment, please give 24-48 hours notice in order to avoid broken appointment fee.

```html
<!DOCTYPE html>
<html lang="en">
<head>
<meta charset="utf-8">
<title>Oswin Family Dentistry – Business Card</title>
<link rel="stylesheet" href="https://fonts.googleapis.com/css2?family=Cinzel:wght@700&family=Arimo:wght@400;700&display=swap">
<style>
  :root {
    --navy: #1f4f94;
    --red: #d7303b;
    --green: #1aa077;
    --orange: #f07a2a;
    --ink: #2a2a2a;
    --paper: #ffffff;
    --backdrop: #e9e6e1;
  }
  * { box-sizing: border-box; margin: 0; padding: 0; }
  html, body {
    width: 1200px; height: 902px; overflow: hidden;
    background: var(--backdrop);
  }
  .canvas { position: relative; width: 1200px; height: 902px; }
  .card {
    position: absolute; width: 660px; height: 377px;
    background: var(--paper);
    box-shadow: 0 6px 18px rgba(0,0,0,.18);
    overflow: hidden;
  }
  .card--back { left: 70px; top: 50px; }
  .card--front { left: 470px; top: 470px; }

  .caps { font-family: "Cinzel", "Copperplate", serif; font-weight: 700; }
  .sans { font-family: "Arimo", Arial, sans-serif; }

  /* back */
  .back-band { position: absolute; inset: 0; width: 100%; height: 100%; }
  .back-title {
    position: absolute; left: 0; right: 0; top: 38px; text-align: center;
    color: var(--paper); font-size: 40px; letter-spacing: 2px;
  }
  .appt-rows { position: absolute; left: 46px; right: 46px; top: 180px; }
  .appt-row {
    display: flex; align-items: baseline; gap: 6px;
    font-size: 21px; color: var(--ink); margin-bottom: 40px;
  }
  .appt-row .fill { flex: 1; border-bottom: 2px dotted #555; height: 1px; }

  /* front */
  .front-art { position: absolute; inset: 0; width: 100%; height: 100%; }
  .brand-mark {
    position: absolute; left: 38px; top: 58px; width: 120px; height: 120px;
    border-radius: 50%; background: var(--navy);
  }
  .brand-name {
    position: absolute; left: 176px; top: 80px;
    color: var(--navy); font-size: 29px; letter-spacing: .5px;
  }
  .brand-slogan {
    position: absolute; left: 176px; top: 126px; width: 444px;
    display: flex; align-items: center; gap: 10px;
    color: var(--red); font-size: 12px; letter-spacing: 1px;
  }
  .brand-slogan::before, .brand-slogan::after {
    content: ""; height: 1.5px; background: var(--red); flex: 1;
  }
  .doctor { position: absolute; font-size: 22px; line-height: 1.05; }
  .doctor .degree { display: block; font-size: 17px; }
  .doctor--left { left: 40px; top: 214px; color: var(--red); }
  .doctor--right { right: 36px; top: 158px; color: var(--navy); text-align: right; }
  .contact { position: absolute; font-size: 17px; color: var(--ink); }
  .contact li { list-style: none; display: flex; align-items: center; gap: 10px; margin-bottom: 6px; }
  .contact--phone { left: 40px; top: 284px; }
  .contact--web { right: 28px; top: 204px; }
  .contact--web li { justify-content: flex-end; }
  .icon { width: 16px; height: 16px; flex: none; }
</style>
</head>
<body>
<main class="canvas">

  <section class="card card--back" aria-label="Appointment card, back side">
    <svg class="back-band" viewBox="0 0 660 377" preserveAspectRatio="none" aria-hidden="true">
      <path d="M0,0 H660 V80 C480,104 220,118 0,150 Z" fill="var(--navy)"/>
      <path d="M0,150 C220,118 480,104 660,80 V86 C480,110 220,124 0,156 Z" fill="var(--red)"/>
    </svg>
    <h2 class="back-title caps">Appointment</h2>
    <div class="appt-rows sans">
      <p class="appt-row">Date<span class="fill"></span>Time<span class="fill"></span>With<span class="fill"></span></p>
      <p class="appt-row">Date<span class="fill"></span>Time<span class="fill"></span>With<span class="fill"></span></p>
      <p class="appt-row">Date<span class="fill"></span>Time<span class="fill"></span>With<span class="fill"></span></p>
    </div>
  </section>

  <section class="card card--front" aria-label="Business card, front side">
    <svg class="front-art" viewBox="0 0 660 377" preserveAspectRatio="none" aria-hidden="true">
      <path d="M0,366 C220,356 470,320 660,258 V270 C470,332 220,368 0,376 Z" fill="var(--green)"/>
      <path d="M0,377 C230,372 480,340 660,282 V377 Z" fill="var(--navy)"/>
    </svg>

    <div class="brand-mark" aria-hidden="true"></div>
    <h1 class="brand-name caps">Oswin Family Dentistry</h1>
    <p class="brand-slogan caps">We give you reasons to smile</p>

    <p class="doctor doctor--right caps">Gerald M Fenwick<span class="degree">DDS</span></p>

    <ul class="contact contact--web sans">
      <li>WWW.BrightmoorToothHaven.Com
        <svg class="icon" viewBox="0 0 16 16" aria-hidden="true"><rect width="16" height="16" rx="3" fill="var(--orange)"/><circle cx="8" cy="8" r="4.5" fill="none" stroke="#fff" stroke-width="1.5"/><path d="M3.5 8h9M8 3.5v9" stroke="#fff" stroke-width="1.2"/></svg>
      </li>
      <li>418 Birch Lane Portland, CT 00000
        <svg class="icon" viewBox="0 0 16 16" aria-hidden="true"><path d="M8 1a5 5 0 0 1 5 5c0 4-5 9-5 9S3 10 3 6a5 5 0 0 1 5-5z" fill="var(--orange)"/><circle cx="8" cy="6" r="1.8" fill="#fff"/></svg>
      </li>
    </ul>

    <p class="doctor doctor--left caps">Bernard K. Oswin<span class="degree">DDS</span></p>

    <ul class="contact contact--phone sans">
      <li>
        <svg class="icon" viewBox="0 0 16 16" aria-hidden="true"><rect width="16" height="16" rx="3" fill="var(--orange)"/><path d="M5 3.5l2 2-1 1.2c.6 1.4 1.6 2.4 3 3L10.3 8.7l2 2-1.3 1.6C7.5 12 4 8.5 3.6 5z" fill="#fff"/></svg>
        555 019 4831
      </li>
      <li>
        <svg class="icon" viewBox="0 0 16 16" aria-hidden="true"><rect width="16" height="16" rx="3" fill="var(--orange)"/><rect x="3.5" y="6" width="9" height="6" rx="1" fill="#fff"/><rect x="5" y="3" width="6" height="3" fill="#fff"/></svg>
        555 019 4832
      </li>
    </ul>
  </section>

</main>
</body>
</html>
```